Create a new business card

I’m looking to update my business card to make it match the rest of my brand. I will include my current website as well as what my vehicle designs look like, etc..
What my business currently services
Weekly maintenance pool openings / closings
Equipment repair, including pumps, heaters, salt systems, filters, etc.
We install automatic covers and maintain them as well as provide preventative maintenance

I would like to include my name.
Dorian Pelkin.
My title
Owner
My email
Dorian@tidewellnx.com
4015827160
Www.tidewellnx.com

```html
<!DOCTYPE html>
<html lang="en">
<head>
<meta charset="utf-8">
<title>Tidewell Pool Service – Business Card</title>
<link href="https://fonts.googleapis.com/css2?family=Montserrat:wght@400;500;600;700&display=swap" rel="stylesheet">
<style>
  :root {
    --page-bg: #1c1d21;
    --navy: #1f3168;
    --sky: #2fa8e0;
    --pool-light: #5cc3ee;
    --pool-deep: #1b93cf;
    --orange: #ef5a1c;
    --ink: #2a2a2a;
    --white: #ffffff;
  }
  * { box-sizing: border-box; margin: 0; padding: 0; }
  html, body { width: 1200px; height: 900px; overflow: hidden; }
  body {
    background: var(--page-bg);
    font-family: "Montserrat", sans-serif;
    display: flex;
    flex-direction: column;
    align-items: center;
    justify-content: center;
    gap: 40px;
  }
  .card {
    position: relative;
    width: 680px;
    height: 388px;
    border-radius: 22px;
    overflow: hidden;
  }

  /* Back side */
  .card-back { color: var(--white); }
  .water {
    position: absolute; inset: 0;
    background: radial-gradient(ellipse at 30% 60%, var(--pool-light), var(--pool-deep) 75%);
  }
  .back-brand {
    position: absolute; left: 60px; top: 150px; width: 250px;
    display: flex; align-items: center; gap: 12px;
    font-weight: 700; font-size: 26px; line-height: 1.15;
  }
  .brand-dot {
    flex: none; width: 22px; height: 22px; border-radius: 50%;
    background: currentColor;
  }
  .divider {
    position: absolute; left: 350px; top: 70px;
    width: 1px; height: 250px; background: rgba(255,255,255,.6);
  }
  .services { position: absolute; left: 385px; top: 95px; }
  .services-title {
    font-weight: 700; font-size: 22px; color: #8fd8ff;
    letter-spacing: .5px; margin-bottom: 12px;
  }
  .services-list { list-style: none; font-size: 14.5px; line-height: 1.75; }
  .services-list li::before { content: "• "; }

  /* Front side */
  .card-front { background: var(--white); }
  .front-bands { position: absolute; inset: 0; }
  .front-brand {
    position: absolute; right: 40px; top: 60px;
    display: flex; align-items: center; gap: 12px;
    color: var(--navy); font-weight: 700; font-size: 26px; line-height: 1.15;
    width: 250px;
  }
  .person { position: absolute; left: 46px; top: 168px; }
  .person-name { color: var(--orange); font-weight: 700; font-size: 30px; }
  .person-title { color: var(--ink); font-size: 15px; margin-top: 2px; }
  .contacts {
    position: absolute; left: 46px; top: 308px;
    list-style: none; color: var(--white); font-size: 15px; line-height: 1.65;
  }
  .contacts li { display: flex; align-items: center; gap: 10px; }
  .contacts svg { width: 14px; height: 14px; fill: var(--sky); flex: none; }
</style>
</head>
<body>

  <section class="card card-back">
    <div class="water" role="img" aria-label="Rippling swimming pool water texture"></div>
    <div class="back-brand"><span class="brand-dot"></span><span>Tidewell Pool Service</span></div>
    <div class="divider"></div>
    <div class="services">
      <h2 class="services-title">OUR SERVICES</h2>
      <ul class="services-list">
        <li>Pool Opening and Closing</li>
        <li>Renovation</li>
        <li>Weekly pool services</li>
        <li>Electronic Leak detection</li>
        <li>Structural Pool Repair</li>
        <li>Equipment repairs and Upgrades</li>
      </ul>
    </div>
  </section>

  <section class="card card-front">
    <svg class="front-bands" viewBox="0 0 680 388" preserveAspectRatio="none" aria-hidden="true">
      <polygon points="0,284 680,96 680,108 0,296" fill="var(--sky)"/>
      <polygon points="0,296 680,108 680,388 0,388" fill="var(--navy)"/>
    </svg>
    <div class="front-brand"><span class="brand-dot"></span><span>Tidewell Pool Service</span></div>
    <div class="person">
      <h1 class="person-name">Dorian Pelkin</h1>
      <p class="person-title">Owner</p>
    </div>
    <ul class="contacts">
      <li>
        <svg viewBox="0 0 24 24"><path d="M6.6 10.8a15.1 15.1 0 0 0 6.6 6.6l2.2-2.2a1 1 0 0 1 1-.25 11.4 11.4 0 0 0 3.6.57 1 1 0 0 1 1 1V20a1 1 0 0 1-1 1A17 17 0 0 1 3 4a1 1 0 0 1 1-1h3.5a1 1 0 0 1 1 1c0 1.25.2 2.45.57 3.57a1 1 0 0 1-.25 1z"/></svg>
        4015827160
      </li>
      <li>
        <svg viewBox="0 0 24 24"><path d="M2 5h20v14H2z M2 5l10 8 10-8" /></svg>
        Dorian@tidewellnx.com
      </li>
      <li>
        <svg viewBox="0 0 24 24"><circle cx="12" cy="12" r="10"/></svg>
        Www.tidewellnx.com
      </li>
    </ul>
  </section>

</body>
</html>
```